Luxury Business Card Design for High-End Window Treatments

Gilded Slatworks
Custom Plantation Shutters & Architectural Shading Systems

⸻

BACK

Daniel Trevick
Owner

Custom Interior & Exterior Window Treatments

919-555-0148
gildedslatworks.com

I have included a picture that I’m hoping we can use on the back, but I’m also wondering if you can get rid of the ladder? Should we get rid of shutters , shades and blinds underneath Gilded Slatworks?

Target Market(s)

High-end residential homeowners, custom home builders, architects, interior designers, and luxury renovation clients seeking premium plantation shutters and motorized architectural shading systems.

Industry/Entity Type

Custom Window treatments

Contact Information for Business Card

Front Gilded Slatworks Custom Plantation Shutters Motorized Architectural Shading Systems BACK Daniel Trevick Owner 919-555-0148 GildedSlatworks.com Custom Interior & Exterior Window Treatments By Appointment

Requirements
Nice to have
• Not 100% sure on nice to halves or the color but you can definitely check out my website to get a better understanding of what I’m trying to do

```html
<!DOCTYPE html>
<html lang="en">
<head>
<meta charset="utf-8">
<title>Gilded Slatworks – Business Card</title>
<link href="https://fonts.googleapis.com/css2?family=Libre+Baskerville:wght@400;700&family=Lato:wght@400;700;900&display=swap" rel="stylesheet">
<style>
  :root {
    --stage: #2b2b2c;
    --card: #0d0d0e;
    --gold: #e8c54b;
    --gold-line: #b9973a;
    --silver: #d9d9dc;
    --white: #f2f2f2;
    --muted: #bdbdbd;
    --strip: #f4f4f4;
    --ink: #1a1a1a;
  }
  * { box-sizing: border-box; margin: 0; padding: 0; }
  html, body { width: 1200px; height: 939px; overflow: hidden; }
  body {
    background: var(--stage);
    position: relative;
    font-family: "Lato", sans-serif;
  }
  .card {
    position: absolute;
    left: 250px;
    width: 700px;
    height: 400px;
    background: var(--card);
    border-radius: 22px;
    overflow: hidden;
  }
  .card--front { top: 40px; }
  .card--back { top: 499px; }

  /* Front */
  .brand {
    position: absolute;
    top: 110px; left: 0; right: 0;
    text-align: center;
  }
  .brand__name {
    font-family: "Libre Baskerville", serif;
    font-weight: 400;
    font-size: 48px;
    color: var(--silver);
    letter-spacing: 1px;
  }
  .brand__lines {
    margin-top: 18px;
    font-family: "Libre Baskerville", serif;
    font-weight: 700;
    font-size: 24px;
    color: var(--gold);
    word-spacing: 22px;
  }
  .front__tagline {
    position: absolute;
    left: 0; right: 0; bottom: 46px;
    text-align: center;
    font-family: "Libre Baskerville", serif;
    font-size: 15px;
    color: var(--white);
    letter-spacing: 0.4px;
  }

  /* Back */
  .person {
    position: absolute;
    left: 40px; top: 96px;
    width: 285px;
    text-align: right;
  }
  .person__name {
    font-family: "Libre Baskerville", serif;
    font-weight: 700;
    font-size: 24px;
    color: var(--white);
    letter-spacing: 0.5px;
    white-space: nowrap;
  }
  .person__role {
    font-size: 15px;
    color: var(--white);
    margin-top: 4px;
  }
  .divider {
    position: absolute;
    left: 345px; top: 58px;
    width: 1px; height: 100px;
    background: var(--muted);
  }
  .contact {
    position: absolute;
    left: 365px; top: 52px;
    list-style: none;
    color: var(--white);
    font-size: 16px;
    line-height: 22px;
  }
  .contact li { display: flex; align-items: flex-start; gap: 10px; margin-bottom: 6px; }
  .contact svg { flex: none; margin-top: 4px; }

  .showcase {
    position: absolute;
    left: 38px; top: 198px;
    width: 624px; height: 176px;
    border: 1px solid var(--gold-line);
  }
  .showcase__title {
    position: absolute;
    top: -13px; left: 40px;
    padding: 0 8px;
    background: var(--card);
    font-family: "Libre Baskerville", serif;
    font-weight: 700;
    font-size: 16px;
    color: var(--gold);
    white-space: nowrap;
  }
  .gallery {
    position: absolute;
    left: 8px; top: 18px; right: 8px; bottom: 8px;
    display: grid;
    grid-template-columns: 110px 110px 1fr;
    grid-template-rows: 1fr 1fr;
    gap: 6px;
  }
  .tile {
    position: relative;
    border: 2px solid var(--strip);
    overflow: hidden;
  }
  .tile--exterior { grid-column: 3; grid-row: 1 / span 2; }
  .tile__photo { position: absolute; inset: 0; }
  .tile__label {
    position: absolute;
    left: 0; right: 0; bottom: 0;
    background: var(--strip);
    color: var(--ink);
    font-weight: 900;
    font-size: 10px;
    letter-spacing: 1px;
    text-align: center;
    padding: 2px 0;
  }
  .photo--shutters { background: linear-gradient(160deg, #f1ede4, #c9bfae); }
  .photo--blinds { background: linear-gradient(170deg, #e9e6e0, #a9a39a); }
  .photo--shades { background: linear-gradient(160deg, #3b3e42, #8a7f70); }
  .photo--drapes { background: linear-gradient(90deg, #55555c, #e8e8ea 50%, #55555c); }
  .photo--exterior { background: linear-gradient(180deg, #8fb4d8 0%, #e7e5df 30%, #3e4246 55%, #cfcac0 100%); }
</style>
</head>
<body>

  <section class="card card--front">
    <div class="brand">
      <h1 class="brand__name">Gilded Slatworks</h1>
      <p class="brand__lines">Shutters Shades Blinds</p>
    </div>
    <p class="front__tagline">Custom Plantation Shutters &amp; Motorized Architectural Shading Systems</p>
  </section>

  <section class="card card--back">
    <div class="person">
      <h2 class="person__name">DANIEL TREVICK</h2>
      <p class="person__role">Owner</p>
    </div>
    <div class="divider"></div>
    <ul class="contact">
      <li>
        <svg width="12" height="15" viewBox="0 0 12 15"><path d="M6 1a4.5 4.5 0 0 0-4.5 4.5C1.5 9 6 14 6 14s4.5-5 4.5-8.5A4.5 4.5 0 0 0 6 1z" fill="none" stroke="#f2f2f2" stroke-width="1.5"/><circle cx="6" cy="5.5" r="1.6" fill="#f2f2f2"/></svg>
        <span>418 Market Row, Suite 210<br>Raleigh, NC 27601</span>
      </li>
      <li>
        <svg width="13" height="13" viewBox="0 0 13 13"><path d="M3 1l2 3-1.2 1.2a7 7 0 0 0 4 4L9 8l3 2-1.2 2A9.5 9.5 0 0 1 1 2.2z" fill="#f2f2f2"/></svg>
        <span>919-555-0148</span>
      </li>
      <li>
        <svg width="13" height="13" viewBox="0 0 13 13"><circle cx="6.5" cy="6.5" r="5.5" fill="none" stroke="#f2f2f2" stroke-width="1.4"/><path d="M1 6.5h11M6.5 1c-2 2.5-2 8.5 0 11M6.5 1c2 2.5 2 8.5 0 11" fill="none" stroke="#f2f2f2" stroke-width="1"/></svg>
        <span>gildedslatworks.com</span>
      </li>
    </ul>

    <div class="showcase">
      <h3 class="showcase__title">CUSTOM INTERIOR &amp; EXTERIOR WINDOW TREATMENTS</h3>
      <div class="gallery">
        <figure class="tile">
          <div class="tile__photo photo--shutters" role="img" aria-label="Room with white plantation shutters on arched windows"></div>
          <figcaption class="tile__label">SHUTTERS</figcaption>
        </figure>
        <figure class="tile">
          <div class="tile__photo photo--blinds" role="img" aria-label="Window fitted with light horizontal blinds"></div>
          <figcaption class="tile__label">BLINDS</figcaption>
        </figure>
        <figure class="tile tile--exterior">
          <div class="tile__photo photo--exterior" role="img" aria-label="Covered porch of a home enclosed with dark exterior screen shades"></div>
          <figcaption class="tile__label">EXTERIOR</figcaption>
        </figure>
        <figure class="tile">
          <div class="tile__photo photo--shades" role="img" aria-label="Living room windows with dark roman shades"></div>
          <figcaption class="tile__label">SHADES</figcaption>
        </figure>
        <figure class="tile">
          <div class="tile__photo photo--drapes" role="img" aria-label="Window dressed with grey drapes and sheer curtains"></div>
          <figcaption class="tile__label">DRAPES</figcaption>
        </figure>
      </div>
    </div>
  </section>

</body>
</html>
```